Delivery Docket urgent plus require many other designs for more stationary after this.

We need a new delivery docket design urgently as the one we have needs updating and we have changed our company name. Please do not copy the one I have uploaded as we do not feel this looks professional enough. I uploaded it as a few designers requested to see what we are currently using thank you.
It is quite complex in that we need a range of information to be on the one docket.
We are a Transport Company based in Australia that has a wide variety of items that we deliver such as water, sand and gravels and heavy equipment transport.
We would prefer to keep this design to A5 size as we will get them made into books. We are looking for a modern professional look. Although it is only a delivery docket this is given to all our customers so needs to look impressive.

We need our new logo on the docket (WTR). There will also need to be areas for our address and contact numbers, email etc these will be supplied to the winning designer to make the final adjustments so for now just put something generic in these spaces.
Needs to have an area for customer details, purchase order number, date and docket number (docket number to be in red)
Needs a section where we can list the type of product / and or service that has been provided and the amount / qty usually 3 lines will be enough for this. Need area under this where the customer can sign name and print name to say that the goods / and or services have been received.

Also required somewhere on the docket are the words, Tax Invoice will be issued based on the information provided on this docket. Conditions on back of page

We then need a separate section on the same page which we will use internally that the staff member can tear off and hand into the office. On this section it needs to have area where the driver can list km at start of job and at end with space to calculate km travelled, details of fuel purchased eg amount and litres, vehicle that is being used. also need to log down wheel bearing temps.
prime mover needs spaces as follows
Steer axel FL____________ Steer axel FR _________ 1st drive axel L_______
1st drive axel R_________ 2nd drive axel L_______ 2nd drive axel R________

For the trailers need something similar x 2 as have 2 trailers
1st axel DS_________ 1st axel PS_________ 2nd axel DS__________
2nd axel PS_________ 3rd axel DS_________ 3rd axel PS__________

I have included a few examples of designs we have used in past and ones that we like so you can get an idea of the colours we prefer, I have included some of the designs we are currently receiving for our logo that I like so you can get idea again of colours we prefer. There is much more we need designed also such as time sheets, more delivery dockets and letter heads so there is a lot of more work available to the winning designer.

Thank you

Customers

Serif
Sans Serif

Designer to choose colors to be used in the design.

• Please don't copy old docket as we do not like it and nned new info on new design thank you

```html
<!DOCTYPE html>
<html lang="en">
<head>
<meta charset="utf-8">
<title>Delivery Docket</title>
<link href="https://fonts.googleapis.com/css2?family=Montserrat:ital,wght@0,400;0,600;0,700;0,800;1,400&display=swap" rel="stylesheet">
<style>
  :root {
    --red: #e3000f;
    --ink: #111111;
    --paper: #ffffff;
    --stage: #5b5b5b;
    --muted: #b4b4b4;
    --body: #1e1e1e;
  }
  * { box-sizing: border-box; margin: 0; padding: 0; }
  html, body { width: 1072px; height: 1200px; overflow: hidden; }
  body { background: var(--stage); font-family: "Montserrat", sans-serif; color: var(--body); }

  .docket { position: absolute; left: 126px; top: 19px; width: 820px; height: 1162px; background: var(--paper); }
  .abs { position: absolute; }

  .title-rule { left: 47px; width: 725px; top: 49px; height: 2px; background: var(--ink); }
  .title-badge { left: 307px; top: 31px; width: 205px; height: 37px; background: var(--red); border: 2px solid var(--paper); outline: 1.5px solid var(--ink); border-radius: 6px; color: #fff; font-weight: 800; font-size: 19px; display: flex; align-items: center; justify-content: center; letter-spacing: .2px; }

  .brand { left: 57px; top: 100px; display: flex; align-items: center; gap: 14px; color: var(--muted); font-weight: 800; font-size: 54px; letter-spacing: 1px; }
  .brand-mark { width: 40px; height: 40px; border-radius: 50%; background: var(--muted); }

  .company { left: 392px; top: 80px; width: 380px; font-size: 15px; }
  .company-name { color: var(--red); font-weight: 700; font-size: 16px; margin-bottom: 4px; }
  .field { display: flex; align-items: baseline; height: 25px; }
  .field .label { white-space: nowrap; padding-right: 4px; }
  .field .fill { flex: 1; border-bottom: 1.5px dotted #444; transform: translateY(-4px); }
  .company .abn { color: var(--red); font-weight: 700; }

  .panel { border: 2px solid var(--ink); border-radius: 7px; overflow: hidden; }
  .panel-head { background: var(--ink); color: #fff; height: 33px; display: flex; align-items: center; font-weight: 700; letter-spacing: 4px; font-size: 18px; }

  .customer { left: 49px; top: 216px; width: 721px; height: 168px; }
  .customer .panel-head { justify-content: space-between; padding: 0 18px 0 16px; }
  .docket-no { color: var(--red); letter-spacing: 0; font-size: 19px; font-weight: 700; }
  .customer-fields { padding: 18px 16px 0 17px; font-size: 16px; }
  .customer-fields .field { height: 29.5px; }
  .customer-fields .gap { width: 8px; }

  .dash { left: 47px; width: 725px; height: 0; border-top: 1.5px dashed #444; }

  .items { left: 49px; top: 408px; width: 721px; height: 250px; }
  .items table { width: 100%; height: 100%; border-collapse: collapse; table-layout: fixed; }
  .items th { background: var(--ink); color: var(--red); font-size: 18px; font-weight: 700; height: 32px; }
  .items th + th, .items td + td { border-left: 2px solid var(--ink); }
  .items td { border-top: 2px solid var(--ink); }
  .items tbody tr:first-child td { border-top: none; }
  .items .col-qty { width: 133px; text-align: left; padding-left: 16px; }
  .items .col-amt { width: 170px; }

  .notice { left: 0; width: 820px; top: 664px; text-align: center; color: var(--red); font-style: italic; font-size: 14.5px; }

  .vehicle { left: 49px; top: 698px; width: 721px; height: 137px; }
  .vehicle .panel-head { justify-content: center; font-size: 19px; letter-spacing: 5px; }
  .vehicle-fields { padding: 14px 10px 0 10px; font-size: 16px; }

  .axles { left: 51px; top: 858px; width: 716px; display: grid; grid-template-columns: 99px 132px 15px 101px 131px 11px 97px 130px; row-gap: 8.4px; align-items: center; color: var(--red); font-size: 13.6px; }
  .axles .box { height: 21px; border: 1.5px solid var(--ink); }

  .sign { top: 1049px; height: 83px; }
  .sign .panel-head { height: 27px; justify-content: center; letter-spacing: 0; font-weight: 400; font-size: 16px; }
  .received { left: 41px; width: 422px; }
  .signed { left: 478px; width: 294px; }
</style>
</head>
<body>
<main class="docket">
  <div class="abs title-rule"></div>
  <h1 class="abs title-badge">DELIVERY DOCKET</h1>

  <div class="abs brand"><span class="brand-mark"></span><span>WTR</span></div>

  <section class="abs company">
    <div class="company-name">COMPANY NAME</div>
    <div class="field"><span class="label">Address:</span><span class="fill"></span></div>
    <div class="field"><span class="label">Contact No:</span><span class="fill"></span></div>
    <div class="field"><span class="label">Email:</span><span class="fill"></span></div>
    <div class="field"><span class="label abn">ABN:</span><span class="fill"></span></div>
  </section>

  <section class="abs panel customer">
    <div class="panel-head"><span>CUSTOMER DETAILS</span><span class="docket-no">DELIVERY DOCKET NO.: 2050</span></div>
    <div class="customer-fields">
      <div class="field"><span class="label">Name</span><span class="fill"></span></div>
      <div class="field"><span class="label">Address&nbsp;&nbsp;</span><span class="fill"></span></div>
      <div class="field"><span class="label">Purchase Order No:</span><span class="fill"></span><span class="gap"></span><span class="label">Date</span><span class="fill" style="flex:0 0 164px"></span></div>
      <div class="field"><span class="label">Contact</span><span class="fill"></span></div>
    </div>
  </section>

  <div class="abs dash" style="top:395px"></div>

  <section class="abs panel items">
    <table>
      <thead><tr><th class="col-qty">Quantity</th><th>Description</th><th class="col-amt">Amount</th></tr></thead>
      <tbody>
        <tr><td></td><td></td><td></td></tr>
        <tr><td></td><td></td><td></td></tr>
        <tr><td></td><td></td><td></td></tr>
        <tr><td></td><td></td><td></td></tr>
        <tr><td></td><td></td><td></td></tr>
        <tr><td></td><td></td><td></td></tr>
      </tbody>
    </table>
  </section>

  <p class="abs notice">Tax invoice will be based on information provided on this&nbsp; docket. Condition on back of page.</p>

  <div class="abs dash" style="top:690px"></div>

  <section class="abs panel vehicle">
    <div class="panel-head">VEHICLE INFORMATION</div>
    <div class="vehicle-fields">
      <div class="field"><span class="label">Km at start</span><span class="fill"></span><span class="label">Km at end</span><span class="fill"></span><span class="label">Km travelled</span><span class="fill"></span></div>
      <div class="field"><span class="label">Details of fuel purchased (litres)</span><span class="fill"></span><span class="label">Amount</span><span class="fill" style="flex:1.3"></span></div>
      <div class="field"><span class="label">Wheel bearing temps</span><span class="fill"></span></div>
    </div>
  </section>

  <div class="abs dash" style="top:847px"></div>

  <section class="abs axles">
    <span>Steer axel FL</span><span class="box"></span><span></span><span>Steer axel FR</span><span class="box"></span><span></span><span>1st drive axel L</span><span class="box"></span>
    <span>1st drive axel R</span><span class="box"></span><span></span><span>2nd drive axel L</span><span class="box"></span><span></span><span>2nd drive axel R</span><span class="box"></span>
    <span>1st axel DS</span><span class="box"></span><span></span><span>1st axel PS</span><span class="box"></span><span></span><span>2nd axel DS</span><span class="box"></span>
    <span>2nd axel PS</span><span class="box"></span><span></span><span>3rd axel DS</span><span class="box"></span><span></span><span>3rd axel PS</span><span class="box"></span>
    <span>1st axel DS</span><span class="box"></span><span></span><span>1st axel PS</span><span class="box"></span><span></span><span>2nd axel DS</span><span class="box"></span>
    <span>2nd axel PS</span><span class="box"></span><span></span><span>3rd axel DS</span><span class="box"></span><span></span><span>3rd axel PS</span><span class="box"></span>
  </section>

  <section class="abs panel sign received"><div class="panel-head">Good Received By</div></section>
  <section class="abs panel sign signed"><div class="panel-head">Signed</div></section>
</main>
</body>
</html>
```